Business Card Update, need to bring life to the card, two sided color

We need a new business card design, are moving and changing addresses and need a new look, we have the logos already attached but need a new style moving forward. Can incorporate the color of the logo (The Green) as well, maybe a solid back? We deal with safety products revolving around static electricity and safety lighting. Would like to keep same font in second logo as well.

Target Market(s)

Electrical Safety, Lighting

Contact Information for Business Card

Dale Fenwick
Vice President
Office: 770-555-4821
Cell: 770-555-3067
dale@tkfenwick.example
www.tkfenwick.example
4700 West Harbor Boulevard
Suite #150
Roswell, GA 30076

Font styles to use
Serif
Sans Serif

Requirements
Must have
• Since 1918
Nice to have
• Could use the 100 Year Logo for back of card, would like the back of card to be the same green as logo.
Should not have
• No black cards please.

```html
<!DOCTYPE html>
<html lang="en">
<head>
<meta charset="utf-8">
<title>T.K. Fenwick – Business Card</title>
<link href="https://fonts.googleapis.com/css2?family=Oswald:wght@600&family=Open+Sans:wght@400;600&family=Arimo:wght@700&display=swap" rel="stylesheet">
<style>
  :root {
    --canvas: #e6e6e6;
    --card-front: #ffffff;
    --green: #0f9a55;
    --green-deep: #0b8749;
    --on-green: #ffffff;
    --on-green-soft: rgba(255,255,255,.75);
    --ink: #2b2b2b;
    --ghost: #efefef;
  }
  * { box-sizing: border-box; margin: 0; padding: 0; }
  html, body { width: 1200px; height: 900px; overflow: hidden; }
  body {
    background: var(--canvas);
    font-family: "Open Sans", Arial, sans-serif;
    position: relative;
  }
  .card {
    position: absolute;
    left: 250px;
    width: 700px;
    height: 400px;
    box-shadow: 0 6px 18px rgba(0,0,0,.18);
    overflow: hidden;
  }

  /* Back side */
  .card-back { top: 40px; background: var(--green); }
  .back-brand {
    position: absolute;
    left: 0; right: 0; top: 150px;
    display: flex; align-items: center; justify-content: center; gap: 22px;
  }
  .back-brand__dot {
    width: 78px; height: 78px; border-radius: 50%;
    border: 3px solid var(--on-green);
    flex: none;
  }
  .back-brand__name {
    font-family: "Arimo", Arial, sans-serif;
    font-weight: 700;
    color: var(--on-green);
    line-height: 1.15;
  }
  .back-brand__name .line-1 { display: block; font-size: 34px; }
  .back-brand__name .line-2 { display: block; font-size: 17px; }
  .back-since {
    position: absolute;
    left: 0; right: 0; bottom: 40px;
    text-align: center;
    font-family: "Arimo", Arial, sans-serif;
    font-weight: 700;
    font-size: 16px;
    letter-spacing: 3px;
    text-transform: uppercase;
    color: var(--on-green-soft);
  }

  /* Front side */
  .card-front { top: 460px; background: var(--card-front); }
  .ghost-mark {
    position: absolute;
    left: 210px; top: 40px;
    width: 300px; height: 300px;
    border-radius: 50%;
    border: 22px solid var(--ghost);
  }
  .ghost-mark__name {
    position: absolute;
    left: 0; right: 0; top: 34px;
    font-family: "Oswald", sans-serif;
    font-weight: 600;
    font-size: 30px;
    color: var(--ghost);
    text-align: center;
  }
  .holder {
    position: absolute;
    left: 60px; top: 150px;
    width: 262px;
    text-align: right;
  }
  .holder__name {
    font-family: "Oswald", sans-serif;
    font-weight: 600;
    font-size: 38px;
    line-height: 1;
    color: var(--green);
    text-transform: uppercase;
    letter-spacing: -.5px;
  }
  .holder__title { font-size: 17px; color: var(--ink); margin-top: 6px; }
  .divider {
    position: absolute;
    left: 342px; top: 137px;
    width: 2px; height: 104px;
    background: var(--green);
  }
  .contact {
    position: absolute;
    left: 362px; top: 135px;
    list-style: none;
    font-size: 17px;
    color: var(--ink);
    line-height: 27px;
  }
  .contact li { display: flex; align-items: center; gap: 12px; white-space: nowrap; }
  .contact svg { width: 14px; height: 14px; flex: none; }
  .contact .label { color: var(--green); font-weight: 600; font-size: 14px; }
  .contact .accent { color: var(--green); }
  .address {
    position: absolute;
    left: 70px; bottom: 34px;
    font-size: 17px;
    line-height: 25px;
    color: var(--ink);
  }
</style>
</head>
<body>

<section class="card card-back" aria-label="Card back">
  <div class="back-brand">
    <span class="back-brand__dot"></span>
    <p class="back-brand__name">
      <span class="line-1">T.K. Fenwick</span>
      <span class="line-2">Manufacturing Company, Inc.</span>
    </p>
  </div>
  <p class="back-since">Since 1918</p>
</section>

<section class="card card-front" aria-label="Card front">
  <div class="ghost-mark">
    <p class="ghost-mark__name">T.K. FENWICK</p>
  </div>

  <div class="holder">
    <h1 class="holder__name">Dale Fenwick</h1>
    <p class="holder__title">Vice President</p>
  </div>

  <span class="divider"></span>

  <ul class="contact">
    <li>
      <svg viewBox="0 0 24 24" fill="none" stroke="#0f9a55" stroke-width="2.4"><path d="M6 3l3 4-2 2c1 3 4 6 7 7l2-2 4 3-2 4C10 21 3 14 2 5z"/></svg>
      <span><span class="label">O</span> 770-555-4821</span>
    </li>
    <li>
      <svg viewBox="0 0 24 24" fill="none" stroke="#0f9a55" stroke-width="2.4"><rect x="6" y="2" width="12" height="20" rx="2"/><path d="M11 18h2"/></svg>
      <span><span class="label">C</span> 770-555-3067</span>
    </li>
    <li>
      <svg viewBox="0 0 24 24" fill="none" stroke="#0f9a55" stroke-width="2.4"><rect x="2" y="5" width="20" height="14"/><path d="M2 5l10 8 10-8"/></svg>
      dale@tkfenwick.example
    </li>
    <li>
      <svg viewBox="0 0 24 24" fill="none" stroke="#0f9a55" stroke-width="2.4"><circle cx="12" cy="12" r="10"/><path d="M2 12h20M12 2c3 3 3 17 0 20M12 2c-3 3-3 17 0 20"/></svg>
      <span>www.<span class="accent">tkfenwick</span>.example</span>
    </li>
  </ul>

  <p class="address">4700 West Harbor Boulevard, Suite #150<br>Roswell, GA 30076</p>
</section>

</body>
</html>
```